Stationary design for new digital markerting company

I need a stationary design for a new digital marketing company called Mossy Lantern.
We work with businesses to help them create and increase their online presence in order to increase awareness of their brand.
The design must keep with the colour schemes of our logo.
I would like a design that stands out but isn't over the top while also being professional and sophisticated.

Target Market(s)

other businesses

Industry/Entity Type

Business Consultant

Font styles to use
Sans Serif

Colors
abd036
ffffff
a54499

Requirements
Must have
• logo, plus the same colour scheme

```html
<!DOCTYPE html>
<html lang="en">
<head>
<meta charset="utf-8">
<title>Mossy Lantern Stationery</title>
<link href="https://fonts.googleapis.com/css2?family=Montserrat:wght@400;600&family=Open+Sans:wght@400;600&display=swap" rel="stylesheet">
<style>
  :root {
    --plum: #8a2274;
    --moss: #8fbc2f;
    --paper: #ffffff;
    --paper-shade: #f4f4f4;
    --desk: #e9e9ea;
    --ink: #4a4a4a;
    --ink-soft: #8a8a8a;
    --ghost: #efefef;
  }
  * { box-sizing: border-box; margin: 0; padding: 0; }
  html, body { width: 1200px; height: 900px; overflow: hidden; }
  body {
    background: var(--desk);
    font-family: "Open Sans", Arial, sans-serif;
    color: var(--ink);
    position: relative;
  }
  .piece {
    position: absolute;
    background: var(--paper);
    box-shadow: 0 2px 6px rgba(0,0,0,.12);
    overflow: hidden;
  }
  .brand-name {
    font-family: "Montserrat", Arial, sans-serif;
    font-weight: 600;
    letter-spacing: .06em;
    text-transform: uppercase;
    color: var(--plum);
    white-space: nowrap;
  }
  .brand-dot {
    display: inline-block;
    border-radius: 50%;
    background: var(--moss);
    vertical-align: middle;
  }
  .tagline {
    font-family: "Montserrat", Arial, sans-serif;
    font-weight: 400;
    letter-spacing: .12em;
    color: var(--ink-soft);
    white-space: nowrap;
  }
  .footer-stripe { position: absolute; left: 0; bottom: 0; width: 100%; }

  /* Letterhead */
  .letterhead { left: 40px; top: 40px; width: 330px; height: 467px; }
  .letterhead .lockup { position: absolute; left: 26px; top: 30px; }
  .letterhead .brand-name { font-size: 13px; }
  .letterhead .brand-dot { width: 16px; height: 16px; margin-right: 6px; }
  .letterhead .tagline { font-size: 6px; margin: 3px 0 0 22px; }
  .contact-block {
    position: absolute; right: 24px; top: 28px;
    border-left: 3px solid var(--moss); padding-left: 6px;
    font-size: 5.5px; line-height: 1.55; color: var(--ink);
  }
  .letter-body {
    position: absolute; left: 26px; right: 26px; top: 110px;
    font-size: 6.5px; line-height: 1.6;
  }
  .letter-body p { margin-bottom: 8px; }
  .letter-sign { margin-top: 14px; }
  .letter-sign strong { display: block; margin-top: 18px; color: var(--plum); font-weight: 600; }

  /* Folder */
  .folder { left: 400px; top: 40px; width: 330px; height: 467px; background: var(--plum); }
  .folder .emblem {
    position: absolute; left: 105px; top: 60px; width: 120px; height: 120px;
    border-radius: 50%; background: var(--moss);
  }
  .folder .lockup { position: absolute; right: 28px; bottom: 60px; text-align: right; }
  .folder .brand-name { color: var(--paper); font-size: 22px; }
  .folder .tagline { color: var(--paper); font-size: 8px; margin-top: 4px; }

  /* Envelope */
  .envelope { left: 760px; top: 40px; width: 400px; height: 190px; }
  .envelope .flap {
    position: absolute; left: 0; top: 0; width: 100%; height: 78px;
    background: var(--plum); border-radius: 0 0 14px 14px;
  }
  .envelope .brand-dot { position: absolute; left: 193px; top: 32px; width: 14px; height: 14px; }

  /* Compliment slip */
  .slip { left: 760px; top: 260px; width: 400px; height: 230px; }
  .slip .ghost-disc {
    position: absolute; right: 30px; top: -40px; width: 150px; height: 150px;
    border-radius: 50%; background: var(--ghost);
  }
  .slip .lockup { position: absolute; left: 30px; top: 120px; }
  .slip .brand-name { font-size: 15px; }
  .slip .brand-dot { width: 18px; height: 18px; margin-right: 7px; }
  .slip .tagline { font-size: 6.5px; margin: 3px 0 0 25px; }
  .slip .address { position: absolute; left: 30px; bottom: 24px; font-size: 6.5px; color: var(--ink); }

  /* Business cards */
  .card { width: 240px; height: 138px; }
  .card-back { left: 40px; top: 540px; }
  .card-front { left: 40px; top: 710px; background: var(--plum); }
  .card-back .lockup { position: absolute; left: 16px; top: 18px; }
  .card-back .brand-name { font-size: 10px; }
  .card-back .brand-dot { width: 12px; height: 12px; margin-right: 5px; }
  .card-back .tagline { font-size: 5px; margin: 2px 0 0 17px; }
  .card-back .person { position: absolute; right: 16px; top: 20px; text-align: right; }
  .person-name { font-family: "Montserrat", Arial, sans-serif; font-weight: 600; font-size: 8px; color: var(--plum); }
  .person-role { font-size: 6px; color: var(--ink-soft); }
  .card-back .contact-block { left: 16px; right: auto; top: 62px; }
  .card-front .lockup { position: absolute; left: 0; right: 0; top: 50px; text-align: center; }
  .card-front .brand-name { color: var(--paper); font-size: 13px; }
  .card-front .brand-dot { width: 16px; height: 16px; margin-right: 6px; }
  .card-front .tagline { color: var(--paper); font-size: 6px; margin-top: 4px; }

  /* Notebook */
  .notebook { left: 860px; top: 520px; width: 300px; height: 340px; background: var(--plum); }
  .notebook .binding {
    position: absolute; left: 8px; top: 10px; bottom: 10px; width: 6px;
    border-left: 2px dotted #5c5c5c;
  }
  .notebook .emblem {
    position: absolute; left: 95px; top: 50px; width: 110px; height: 110px;
    border-radius: 50%; background: var(--moss);
  }
  .notebook .lockup { position: absolute; right: 24px; bottom: 46px; text-align: right; }
  .notebook .brand-name { color: var(--paper); font-size: 19px; }
  .notebook .tagline { color: var(--paper); font-size: 7px; margin-top: 4px; }

  /* Small items */
  .pencil { position: absolute; height: 10px; border-radius: 2px; }
  .pencil-plum { left: 330px; top: 600px; width: 360px; background: var(--plum); }
  .pencil-moss { left: 330px; top: 625px; width: 360px; background: var(--moss); }
  .pencil::after {
    content: ""; position: absolute; right: -14px; top: 0;
    border-left: 14px solid #d9b98a; border-top: 5px solid transparent; border-bottom: 5px solid transparent;
  }
  .keytag {
    left: 330px; top: 680px; width: 180px; height: 80px; border-radius: 10px;
    background: var(--paper-shade); border: 2px solid #d0d0d0;
  }
  .keytag .ring {
    position: absolute; left: 10px; top: 30px; width: 16px; height: 16px;
    border-radius: 50%; border: 2px solid #b5b5b5;
  }
  .keytag .lockup { position: absolute; left: 40px; top: 31px; }
  .keytag .brand-name { font-size: 10px; }
  .keytag .brand-dot { width: 12px; height: 12px; margin-right: 5px; }
  .eraser { left: 540px; top: 690px; width: 160px; height: 60px; background: var(--plum); }
  .eraser .sleeve { position: absolute; left: 0; top: 0; width: 30px; height: 100%; background: var(--paper); }
  .eraser .lockup { position: absolute; left: 40px; top: 23px; }
  .eraser .brand-name { color: var(--paper); font-size: 9px; }
  .eraser .brand-dot { width: 11px; height: 11px; margin-right: 4px; }
</style>
</head>
<body>

  <section class="piece letterhead">
    <div class="lockup">
      <div class="brand-name"><span class="brand-dot"></span>Mossy Lantern</div>
      <div class="tagline">Bright Ideas for Online Growth</div>
    </div>
    <address class="contact-block">
      1300 555 018<br>hello@mosslantern.com<br>www.mosslantern.com<br>Suite 9, 22 Fernhill Road, Brookvale
    </address>
    <div class="letter-body">
      <p>Dear Sir,</p>
      <p>Thank you for meeting with our team last week. We are pleased to share a summary of the plan we discussed for growing your online presence over the coming months.</p>
      <p>Our approach starts with a clear audit of your current channels, followed by search, content and social work that builds steady awareness of your brand with the right audience.</p>
      <p>Please review the attached proposal and let us know a convenient time to talk through the next steps together.</p>
      <div class="letter-sign">Yours sincerely,<strong>Mara Quill</strong>Managing Director</div>
    </div>
    <svg class="footer-stripe" width="330" height="26" viewBox="0 0 330 26" aria-hidden="true">
      <polygon points="0,26 250,8 250,11 0,26" fill="var(--plum)"/>
      <polygon points="250,8 330,0 330,6 250,11" fill="var(--moss)"/>
    </svg>
  </section>

  <section class="piece folder">
    <div class="emblem"></div>
    <div class="lockup">
      <div class="brand-name">Mossy Lantern</div>
      <div class="tagline">Bright Ideas for Online Growth</div>
    </div>
  </section>

  <section class="piece envelope">
    <div class="flap"></div>
    <span class="brand-dot"></span>
  </section>

  <section class="piece slip">
    <div class="ghost-disc"></div>
    <div class="lockup">
      <div class="brand-name"><span class="brand-dot"></span>Mossy Lantern</div>
      <div class="tagline">Bright Ideas for Online Growth</div>
    </div>
    <div class="address">Suite 9, 22 Fernhill Road, Brookvale</div>
    <svg class="footer-stripe" width="400" height="26" viewBox="0 0 400 26" aria-hidden="true">
      <polygon points="0,26 300,8 300,11 0,26" fill="var(--plum)"/>
      <polygon points="300,8 400,0 400,6 300,11" fill="var(--moss)"/>
    </svg>
  </section>

  <section class="piece card card-back">
    <div class="lockup">
      <div class="brand-name"><span class="brand-dot"></span>Mossy Lantern</div>
      <div class="tagline">Bright Ideas for Online Growth</div>
    </div>
    <div class="person">
      <div class="person-name">Rowan Ellery</div>
      <div class="person-role">Marketing Director</div>
    </div>
    <address class="contact-block">
      1300 555 018<br>hello@mosslantern.com<br>www.mosslantern.com<br>Suite 9, 22 Fernhill Road, Brookvale
    </address>
    <svg class="footer-stripe" width="240" height="20" viewBox="0 0 240 20" aria-hidden="true">
      <polygon points="0,20 180,6 180,9 0,20" fill="var(--plum)"/>
      <polygon points="180,6 240,0 240,5 180,9" fill="var(--moss)"/>
    </svg>
  </section>

  <section class="piece card card-front">
    <div class="lockup">
      <div class="brand-name"><span class="brand-dot"></span>Mossy Lantern</div>
      <div class="tagline">Bright Ideas for Online Growth</div>
    </div>
  </section>

  <div class="pencil pencil-plum"></div>
  <div class="pencil pencil-moss"></div>

  <section class="piece keytag">
    <div class="ring"></div>
    <div class="lockup">
      <div class="brand-name"><span class="brand-dot"></span>Mossy Lantern</div>
    </div>
  </section>

  <section class="piece eraser">
    <div class="sleeve"></div>
    <div class="lockup">
      <div class="brand-name"><span class="brand-dot"></span>Mossy Lantern</div>
    </div>
  </section>

  <section class="piece notebook">
    <div class="binding"></div>
    <div class="emblem"></div>
    <div class="lockup">
      <div class="brand-name">Mossy Lantern</div>
      <div class="tagline">Bright Ideas for Online Growth</div>
    </div>
  </section>

</body>
</html>
```